larkforge website

commerce website to sell cookeries, brackets, mailboxes and to show off homes built. Modern Steel in design see marlo cycles web page to be like: https://www.marlocycles-demo.com/en/ sorry its bright nest hosting word press divi

must be able to add products to page

Target Market(s)

mainly western states of U.S.

Industry/Entity Type

Building Product

Coding

Coded - Design and coding required

Number of Pages Required

3 page

Font styles to use
Sans Serif

Colors

Designer to choose colors to be used in the design.

Requirements
Must have
• customers to be able to order products from page
• bright nest hosting word press divi

```html
<!DOCTYPE html>
<html lang="en">
<head>
<meta charset="utf-8">
<title>Larkforge — Modern Steel</title>
<link rel="stylesheet" href="https://fonts.googleapis.com/css2?family=Montserrat:wght@400;500;600;700;800&display=swap">
<style>
:root{
  --navy:#2f4068;
  --navy-dark:#263658;
  --navy-deep:#1f2c49;
  --ink:#222;
  --text:#444;
  --muted:#888;
  --line:#e2e2e2;
  --white:#fff;
  --footer:#121212;
  --fire:#e8752a;
}
*{box-sizing:border-box;margin:0;padding:0}
html,body{width:1200px;height:3720px;overflow:hidden}
body{font-family:"Montserrat",sans-serif;color:var(--ink);background:var(--white);position:relative}
a{color:inherit;text-decoration:none}
.abs{position:absolute}

/* header */
.topbar{position:absolute;left:0;top:0;width:1200px;height:95px;background:var(--navy)}
.brand{position:absolute;left:170px;top:22px;display:flex;align-items:center;gap:10px;color:var(--white);font-weight:600;font-size:24px;letter-spacing:1px}
.brand .dot{width:22px;height:22px;border-radius:50%;background:var(--white)}
.search{position:absolute;left:344px;top:26px;width:354px;height:40px;display:flex;background:var(--white);border-radius:3px;overflow:hidden}
.search span{flex:1;font-size:11px;color:#999;padding:13px 12px}
.search .btn{width:42px;background:#222;display:flex;align-items:center;justify-content:center}
.acct{position:absolute;top:36px;color:var(--white);font-size:11px;line-height:14px}
.acct b{font-weight:700;font-size:12px}
.cart{position:absolute;left:944px;top:34px;display:flex;align-items:center;gap:8px;color:var(--white);font-size:11px}
.nav{position:absolute;left:0;top:95px;width:1200px;height:54px;background:var(--navy-dark)}
.nav a{position:absolute;top:20px;color:var(--white);font-size:12px;font-weight:600;letter-spacing:.3px}

/* hero */
.hero{position:absolute;left:0;top:149px;width:1200px;height:531px;background:radial-gradient(ellipse at 50% 70%,#c8591d 0%,#5a3420 28%,#223024 60%,#1b2433 100%)}
.hero h1{position:absolute;left:0;right:0;top:208px;text-align:center;color:var(--white);font-size:88px;font-weight:800;letter-spacing:2px}
.hero .arr{position:absolute;top:248px}

/* promo tiles */
.tile{position:absolute;top:723px;width:415px;height:203px;background:linear-gradient(90deg,#d6d6d6,#f3f3f3 55%,#e0e0e0);overflow:hidden}
.tile .photo{position:absolute;right:0;top:0;width:205px;height:203px;border-radius:110px 0 0 110px}
.tile h3{position:absolute;left:32px;top:68px;color:var(--navy);font-size:18px;font-weight:600}
.tile p{position:absolute;left:28px;top:98px;width:190px;font-size:17px;line-height:23px;color:#333}

/* section heads */
.h2{position:absolute;left:172px;font-size:26px;font-weight:700;color:var(--ink)}
.tab-off{color:#8a8a8a}
.pager{position:absolute;font-size:14px;color:#333;display:flex;gap:18px}

/* product cards */
.card{position:absolute;width:201px;height:331px;border:1px solid var(--line);border-radius:4px;background:var(--white);text-align:center}
.card.lift{box-shadow:0 4px 14px rgba(0,0,0,.18);border-color:#f0f0f0}
.card .pic{margin:11px auto 0;width:179px;height:149px;border-radius:4px}
.card .name{margin-top:20px;font-size:12.5px;line-height:19px;color:#333}
.card .price{margin-top:8px;font-size:15px;font-weight:700;color:var(--navy)}
.card .price s{font-size:12px;font-weight:400;color:#777;margin-left:4px}
.card .shop{position:absolute;left:25px;top:262px;width:150px;height:42px;border:1.5px solid var(--navy);border-radius:2px;color:var(--navy);font-size:11px;font-weight:700;display:flex;align-items:center;justify-content:center;gap:8px}
.card .shop.solid{background:var(--navy);color:var(--white)}

/* offer band */
.offer{position:absolute;left:0;top:1445px;width:1200px;height:406px;background:linear-gradient(90deg,rgba(47,64,104,.95),rgba(47,64,104,.85)),linear-gradient(180deg,#3a3a3a,#6a4a30)}
.offer h3{position:absolute;left:172px;top:94px;color:var(--white);font-size:27px;font-weight:700}
.offer p{position:absolute;left:172px;top:142px;width:380px;color:var(--white);font-size:22px;line-height:32px;font-weight:500}
.offer .cta{position:absolute;left:172px;top:227px;width:150px;height:42px;border:2px solid var(--white);color:var(--white);font-size:11px;font-weight:700;display:flex;align-items:center;justify-content:center;gap:8px}
.offer .art{position:absolute;left:540px;top:55px;width:580px;height:300px;background:radial-gradient(ellipse,rgba(255,255,255,.25),rgba(255,255,255,0) 70%)}

/* blog */
.blog-pic{position:absolute}
.blog-text{position:absolute;background:linear-gradient(180deg,#e9e9e9,#d3d3d3);text-align:center}
.blog-text .date{font-size:11.5px;color:#333;margin-top:28px}
.blog-text .t{margin-top:18px;font-size:15px;line-height:24px;color:#333}
.blog-text .more{margin-top:20px;font-size:12.5px;font-weight:700;color:var(--navy)}

/* service box */
.services{position:absolute;left:172px;top:2849px;width:240px;height:364px;background:var(--navy)}
.svc{position:absolute;left:18px;display:flex;gap:14px;align-items:center;color:var(--white)}
.svc b{display:block;font-size:15px;font-weight:600}
.svc small{display:block;font-size:10.5px;margin-top:2px}

/* deal */
.deal-head{position:absolute;left:437px;top:2848px;font-size:22px;font-weight:700}
.deal-nav{position:absolute;top:2853px;font-size:12.5px;color:#666}
.deal{position:absolute;left:437px;top:2885px;width:590px;height:328px;border:1px solid var(--line)}
.deal .pic{position:absolute;left:17px;top:18px;width:258px;height:290px;background:radial-gradient(ellipse at 50% 45%,#f2a23a 0%,#b8501d 30%,#3a3330 62%,#4d4a44 100%)}
.deal h4{position:absolute;left:296px;top:33px;font-size:18px;font-weight:500;color:#333}
.deal .stars{position:absolute;left:296px;top:63px;font-size:10px;color:#999;letter-spacing:2px}
.deal .dprice{position:absolute;left:296px;top:86px;font-size:16px;color:var(--navy);font-weight:500}
.deal p{position:absolute;left:296px;top:120px;width:275px;font-size:10.5px;line-height:19px;color:#444}
.count{position:absolute;top:222px;width:46px;text-align:center}
.count .n{height:54px;background:var(--navy-deep);color:var(--white);font-size:17px;font-weight:700;line-height:54px}
.count .l{font-size:9.5px;color:#555;margin-top:8px}

/* newsletter */
.news{position:absolute;left:0;top:3277px;width:1200px;height:102px;background:var(--navy-dark)}
.news h3{position:absolute;left:200px;top:39px;color:var(--white);font-size:18px;font-weight:500;letter-spacing:.5px}
.news .field{position:absolute;left:426px;top:31px;width:422px;height:40px;background:var(--white);font-size:11px;color:#555;padding:14px 12px}
.news .sub{position:absolute;left:848px;top:31px;width:125px;height:40px;background:#151d30;color:var(--white);font-size:13px;font-weight:600;display:flex;align-items:center;justify-content:center}

/* footer */
.footer{position:absolute;left:0;top:3379px;width:1200px;height:341px;background:var(--footer);overflow:hidden}
.footer .glow{position:absolute;right:0;bottom:0;width:380px;height:200px;background:radial-gradient(ellipse at 75% 80%,#d4611e 0%,#5a2a12 35%,rgba(18,18,18,0) 75%)}
.f-brand{position:absolute;left:172px;top:88px;display:flex;align-items:center;gap:10px;color:var(--white);font-size:26px;font-weight:600;letter-spacing:1px}
.f-brand .dot{width:24px;height:24px;border-radius:50%;background:var(--white)}
.social{position:absolute;left:184px;top:190px;display:flex;gap:18px}
.social i{display:block;width:14px;height:14px;border-radius:50%;background:var(--white)}
.fcol{position:absolute;top:46px;color:var(--white)}
.fcol h5{font-size:14px;font-weight:500}
.fcol .dash{width:20px;height:2px;background:var(--white);margin:16px 0 12px}
.fcol a{display:block;font-size:10px;line-height:20px;color:#bbb}
.f-rule{position:absolute;left:172px;top:274px;width:855px;height:1px;background:#333}
.copy{position:absolute;left:0;right:0;top:303px;text-align:center;font-size:10.5px;color:#bbb}
.copy span{margin-left:14px}
</style>
</head>
<body>

<header>
  <div class="topbar">
    <a class="brand" href="#"><span class="dot"></span>LARKFORGE</a>
    <div class="search"><span>Search here</span><div class="btn">
      <svg width="12" height="12" viewBox="0 0 12 12"><circle cx="5" cy="5" r="3.6" fill="none" stroke="#fff" stroke-width="1.6"/><line x1="7.6" y1="7.6" x2="11" y2="11" stroke="#fff" stroke-width="1.6"/></svg>
    </div></div>
    <div class="acct" style="left:724px">Hello, Sign in<br><b>Account &amp; Lists ▾</b></div>
    <div class="acct" style="left:855px">Returns<br><b>&amp; Orders ▾</b></div>
    <div class="cart">
      <svg width="28" height="24" viewBox="0 0 28 24"><path d="M4 7h20l-2 15H6z" fill="none" stroke="#fff" stroke-width="1.6"/><path d="M10 7V5a4 4 0 0 1 8 0v2" fill="none" stroke="#fff" stroke-width="1.6"/></svg>
      (0 items)
    </div>
  </div>
  <nav class="nav">
    <a href="#" style="left:185px">HOME</a>
    <a href="#" style="left:267px">ALL PRODUCTS</a>
    <a href="#" style="left:407px">SHOP BY BRAND</a>
    <a href="#" style="left:556px">AFFILIATE</a>
    <a href="#" style="left:666px">SPECIAL</a>
    <a href="#" style="left:765px">ABOUT US</a>
    <a href="#" style="left:874px">BLOG</a>
    <a href="#" style="left:952px">CONTACT</a>
  </nav>
</header>

<section class="hero" role="img" aria-label="Friends toasting drinks around an evening fire pit">
  <h1>LARKFORGE</h1>
  <svg class="arr" style="left:30px" width="18" height="34" viewBox="0 0 18 34"><path d="M16 2L2 17l14 15" fill="none" stroke="#fff" stroke-width="2"/></svg>
  <svg class="arr" style="left:1163px" width="18" height="34" viewBox="0 0 18 34"><path d="M2 2l14 15L2 32" fill="none" stroke="#fff" stroke-width="2"/></svg>
</section>

<section>
  <div class="tile" style="left:172px">
    <h3>LARKFORGE</h3>
    <p>Sed ut perspicunde omnis iste natus</p>
    <div class="photo" role="img" aria-label="Stone fire ring on a lawn with chairs" style="background:radial-gradient(circle at 45% 60%,#e2782a 0%,#7d6d5e 28%,#9a9386 50%,#4f6b34 80%)"></div>
  </div>
  <div class="tile" style="left:612px">
    <h3>MOST POPULAR</h3>
    <p>Sed ut perspicunde omnis iste natus</p>
    <div class="photo" role="img" aria-label="Steel fire bowl burning on gravel" style="background:radial-gradient(circle at 50% 45%,#f3a33a 0%,#b9521d 25%,#2c2a28 50%,#8a8680 80%)"></div>
  </div>
</section>

<section>
  <h2 class="h2" style="top:978px">New Arrival <span class="tab-off" style="margin-left:26px">Best Seller</span></h2>
  <div class="pager" style="left:994px;top:998px"><span>‹</span><span>›</span></div>

  <article class="card" style="left:172px;top:1045px"><div class="pic" role="img" aria-label="Logs burning in a round fire pit" style="background:radial-gradient(circle at 50% 55%,#f6a53a,#c04a1a 40%,#3a2a24 80%)"></div><div class="name">Sed ut perspiciatis<br>koremudomnis stenatus</div><div class="price">$ 128.00<s>$125.000</s></div><a class="shop" href="#">SHOP NOW →</a></article>
  <article class="card lift" style="left:390px;top:1045px"><div class="pic" role="img" aria-label="Fire pit on a lakeside at dusk" style="background:linear-gradient(180deg,#b9b3a8,#6e6a62 45%,#3b3530)"></div><div class="name">Sed ut perspiciatis<br>koremudomnis stenatus</div><div class="price">$ 128.00<s>$125.000</s></div><a class="shop solid" href="#">SHOP NOW →</a></article>
  <article class="card" style="left:608px;top:1045px"><div class="pic" role="img" aria-label="Group gathered around a steel fire pit" style="background:radial-gradient(circle at 50% 75%,#e4782c,#6a5043 35%,#40463a 75%)"></div><div class="name">Sed ut perspiciatis<br>koremudomnis stenatus</div><div class="price">$ 128.00<s>$125.000</s></div><a class="shop" href="#">SHOP NOW →</a></article>
  <article class="card" style="left:825px;top:1045px"><div class="pic" role="img" aria-label="Patio lounge set around a fire table" style="background:linear-gradient(180deg,#3c4a66,#2b3345 50%,#3f3a36)"></div><div class="name">Sed ut perspiciatis<br>koremudomnis stenatus</div><div class="price">$ 128.00<s>$125.000</s></div><a class="shop" href="#">SHOP NOW →</a></article>
</section>

<section class="offer">
  <h3>GET 50% OFF</h3>
  <p>Sed ut perspiciatis unde omnis natus error sit voluptatem</p>
  <a class="cta" href="#">SHOP NOW →</a>
  <div class="art" role="img" aria-label="Faint fire glow backdrop"></div>
</section>

<section>
  <h2 class="h2" style="top:1884px">Featured Products</h2>
  <div class="pager" style="left:994px;top:1906px"><span>‹</span><span>›</span></div>

  <article class="card" style="left:172px;top:1954px"><div class="pic" role="img" aria-label="Concrete fire bowl with flames" style="background:linear-gradient(180deg,#6d8a52 0%,#e89a35 30%,#4d545c 55%,#6a7078)"></div><div class="name">Sed ut perspiciatis<br>koremudomnis stenatus</div><div class="price">$ 128.00<s>$125.000</s></div><a class="shop" href="#">SHOP NOW →</a></article>
  <article class="card" style="left:390px;top:1954px"><div class="pic" role="img" aria-label="Black steel fire pit burning wood" style="background:linear-gradient(180deg,#8a8e88,#d97a2c 40%,#1e1e1e 65%,#3a3a38)"></div><div class="name">Sed ut perspiciatis<br>koremudomnis stenatus</div><div class="price">$ 128.00<s>$125.000</s></div><a class="shop" href="#">SHOP NOW →</a></article>
  <article class="card lift" style="left:608px;top:1954px"><div class="pic" role="img" aria-label="Stone fire pit glowing at night" style="background:radial-gradient(circle at 50% 55%,#ffc35a,#d6682a 25%,#7a5a40 55%,#3d3429)"></div><div class="name">Sed ut perspiciatis<br>koremudomnis stenatus</div><div class="price">$ 128.00<s>$125.000</s></div><a class="shop solid" href="#">SHOP NOW →</a></article>
  <article class="card" style="left:825px;top:1954px"><div class="pic" role="img" aria-label="Brick fire ring in a garden" style="background:radial-gradient(circle at 55% 65%,#e0762c,#6e6a60 35%,#3f5a3a 80%)"></div><div class="name">Sed ut perspiciatis<br>koremudomnis stenatus</div><div class="price">$ 128.00<s>$125.000</s></div><a class="shop" href="#">SHOP NOW →</a></article>
</section>

<section>
  <h2 class="h2" style="top:2338px">From The Blog</h2>

  <div class="blog-pic" role="img" aria-label="Fire pit on a patio with lanterns" style="left:172px;top:2404px;width:201px;height:185px;background:linear-gradient(180deg,#5a6a48,#9e8a74 45%,#3a342e)"></div>
  <div class="blog-text" style="left:172px;top:2589px;width:201px;height:185px"><div class="date">📅30/01/2020</div><div class="t">Sed ut perspiceste<br>natusSed ut persp<br>icundeste natus</div><div class="more">READ MORE</div></div>

  <div class="blog-text" style="left:384px;top:2404px;width:201px;height:185px"><div class="date">📅30/01/2020</div><div class="t">Sed ut perspiceste<br>natusSed ut persp<br>icundeste natus</div><div class="more">READ MORE</div></div>
  <div class="blog-pic" role="img" aria-label="Logs burning in a steel fire pit" style="left:384px;top:2589px;width:201px;height:185px;background:radial-gradient(circle at 50% 55%,#f0903a,#8a3c1a 35%,#4a5a3c 75%)"></div>

  <div class="blog-pic" role="img" aria-label="Family warming hands by an outdoor fire" style="left:599px;top:2404px;width:428px;height:370px;background:radial-gradient(ellipse at 30% 65%,#f3a03a,#b4501c 25%,#5c5a50 55%,#6f8a5a 90%)"></div>
  <div class="blog-text" style="left:826px;top:2589px;width:201px;height:185px"><div class="date">📅30/01/2020</div><div class="t">Sed ut perspiceste<br>natusSed ut persp<br>icundeste natus</div><div class="more">READ MORE</div></div>
</section>

<section>
  <div class="services">
    <div class="svc" style="top:32px">
      <svg width="38" height="38" viewBox="0 0 38 38"><rect x="6" y="5" width="26" height="24" rx="4" fill="#fff"/><rect x="10" y="9" width="18" height="8" fill="#2f4068"/><circle cx="12" cy="31" r="3" fill="#fff"/><circle cx="26" cy="31" r="3" fill="#fff"/></svg>
      <div><b>Fast Delivery</b><small>Ducimus qui blanditiis</small></div></div>
    <div class="svc" style="top:121px">
      <svg width="38" height="38" viewBox="0 0 38 38"><path d="M12 17v-5a7 7 0 0 1 14 0v5" fill="none" stroke="#fff" stroke-width="3"/><rect x="8" y="17" width="22" height="17" rx="2" fill="#fff"/></svg>
      <div><b>100% Satisfaction</b><small>Ducimus qui blanditiis</small></div></div>
    <div class="svc" style="top:205px">
      <svg width="38" height="38" viewBox="0 0 38 38"><circle cx="19" cy="19" r="15" fill="none" stroke="#fff" stroke-width="3"/><path d="M19 10v10h-7" fill="none" stroke="#fff" stroke-width="3"/></svg>
      <div><b>30 Day Money Back</b><small>Ducimus qui blanditiis</small></div></div>
    <div class="svc" style="top:292px">
      <svg width="38" height="38" viewBox="0 0 38 38"><circle cx="19" cy="12" r="8" fill="#fff"/><path d="M4 36a15 13 0 0 1 30 0z" fill="#fff"/></svg>
      <div><b>Support</b><small>Ducimus qui blanditiis</small></div></div>
  </div>

  <h2 class="deal-head">Deal Of The Week</h2>
  <div class="deal-nav" style="left:846px">Previous Deal</div>
  <div class="deal-nav" style="left:962px">Next Deal</div>
  <div class="deal">
    <div class="pic" role="img" aria-label="Steel fire bowl with tall flames on gravel"></div>
    <h4>Sed ut perspicundeste natus</h4>
    <div class="stars">☆☆☆☆☆</div>
    <div class="dprice">$110.00</div>
    <p>Sed ut perspiciatis unde omnis iste natus errorsit voluptatem accusantium doloremque lau dan tum, totam rem aperiam, eaque ipsa quae ab illo inve ntore veritatis et quasi architect</p>
    <div class="count" style="left:296px"><div class="n">316</div><div class="l">Days</div></div>
    <div class="count" style="left:348px"><div class="n">11</div><div class="l">Hours</div></div>
    <div class="count" style="left:400px"><div class="n">57</div><div class="l">Mins</div></div>
    <div class="count" style="left:452px"><div class="n">53</div><div class="l">Secs</div></div>
  </div>
</section>

<section class="news">
  <h3>NEWSLETTER SIGN UP</h3>
  <div class="field">Email address</div>
  <a class="sub" href="#">SUBSCRIBE</a>
</section>

<footer class="footer">
  <div class="glow" role="img" aria-label="Fire bowl glowing in the dark"></div>
  <div class="f-brand"><span class="dot"></span>LARKFORGE</div>
  <div class="social" aria-label="Social links"><i></i><i></i><i></i><i></i><i></i></div>
  <div class="fcol" style="left:401px"><h5>Products</h5><div class="dash"></div>
    <a>Lrem ipsum dolor</a><a>St amet,</a><a>Consectetur</a><a>Sadipscing elit</a><a>Sed do eiusm</a><a>Consectetur</a></div>
  <div class="fcol" style="left:582px"><h5>Company</h5><div class="dash"></div>
    <a>About Us</a><a>Product Reviews</a><a>Privacy Policy</a><a>Terms &amp; Conditions</a><a>Site Map</a><a>Discount Policies</a><a>Advanced Search</a></div>
  <div class="fcol" style="left:755px"><h5>My Account</h5><div class="dash"></div>
    <a>My Account</a><a>Order History</a><a>Wish List</a><a>Newsletter</a></div>
  <div class="fcol" style="left:913px"><h5>Customer Care</h5><div class="dash"></div>
    <a>Order Info</a><a>Shipping / Tracking Info</a><a>Returns Info</a><a>Request Exchange</a><a>Guarantee</a></div>
  <div class="f-rule"></div>
  <div class="copy">Copyright © 2020 Larkforge. All rights reserved<span>Privacy Policy</span><span>Terms &amp; Conditions</span></div>
</footer>

</body>
</html>
```